Boutique custom software development company needs new business card

Our nearly 20 year old custom software development company would like to better include the fact that we are now providing Bitcoin services. These new services are B2B include education (how to acquire and securely hold Bitcoin) and integrating Bitcoin payments into existing ecommerce sites or other existing systems. Please keep the card clean and simple. Attached is our current design and some other files. vextorial.com

Target Market(s)

businesses owners interested in long term relationship

Industry/Entity Type

Custom software development and Bitcoin

Contact Information for Business Card

Dale Parker, dale@vextorial.com, vextorial.com, (888) 555-VXTRL

Font styles to use
Other font styles liked:
• monospace

Requirements
Must have
• double-sided
Nice to have
• clean and simple
Should not have
• physical address

```html
<!DOCTYPE html>
<html lang="en">
<head>
<meta charset="utf-8">
<title>Vextorial business card</title>
<link rel="stylesheet" href="https://fonts.googleapis.com/css2?family=Barlow+Condensed:ital,wght@1,700&family=Lato:wght@300&family=Montserrat:wght@400;700&display=swap">
<style>
  :root {
    --bg: #161616;
    --card: #262626;
    --orange: #f47b20;
    --blue: #3d78c5;
    --white: #f2f2f2;
  }
  * { margin: 0; padding: 0; box-sizing: border-box; }
  html, body { width: 1200px; height: 900px; overflow: hidden; background: var(--bg); }
  .canvas { position: relative; width: 1200px; height: 900px; }
  .card {
    position: absolute; left: 250px; width: 700px; height: 400px;
    background: var(--card); border-radius: 22px;
    box-shadow: 0 10px 30px rgba(0,0,0,.5);
  }
  .card-front { top: 40px; }
  .card-back { top: 460px; }

  .brand { position: absolute; left: 0; right: 0; top: 130px; text-align: center; }
  .brand-name {
    font-family: "Montserrat", sans-serif; font-weight: 700;
    font-size: 84px; letter-spacing: 1px; color: var(--blue); line-height: 1;
  }
  .brand-tagline {
    font-family: "Lato", sans-serif; font-weight: 300;
    font-size: 27px; color: var(--blue); margin-top: 10px; letter-spacing: -0.3px;
  }

  .person { position: absolute; left: 120px; top: 110px; text-align: right; width: 250px; }
  .person-name {
    font-family: "Barlow Condensed", sans-serif; font-style: italic; font-weight: 700;
    font-size: 50px; line-height: 1; letter-spacing: 1px; text-transform: uppercase;
  }
  .person-first { color: var(--orange); }
  .person-last { color: var(--blue); }
  .person-title {
    font-family: "Montserrat", sans-serif; font-size: 17px; color: var(--white);
    letter-spacing: 1px; margin-top: 4px;
  }
  .divider { position: absolute; left: 392px; top: 108px; width: 1px; height: 100px; background: var(--blue); }
  .contact { position: absolute; left: 410px; top: 118px; list-style: none; }
  .contact li {
    font-family: "Montserrat", sans-serif; font-size: 17px; color: var(--white);
    display: flex; align-items: center; gap: 8px; height: 27px; white-space: nowrap;
  }
  .contact svg { width: 12px; height: 12px; flex: none; }
  .contact .site { color: var(--blue); }
  .services {
    position: absolute; left: 0; right: 0; top: 285px; text-align: center;
    font-family: "Montserrat", sans-serif; font-size: 17px; color: var(--white); letter-spacing: .3px;
  }
  .services-accent { color: var(--orange); }
</style>
</head>
<body>
<main class="canvas">
  <section class="card card-front">
    <div class="brand">
      <div class="brand-name">Vextorial</div>
      <div class="brand-tagline">developer of custom applications</div>
    </div>
  </section>

  <section class="card card-back">
    <div class="person">
      <div class="person-name"><span class="person-first">Dale</span> <span class="person-last">Parker</span></div>
      <div class="person-title">DIRECTOR</div>
    </div>
    <div class="divider"></div>
    <ul class="contact">
      <li>
        <svg viewBox="0 0 12 12" aria-hidden="true"><path d="M3 1 L5 3 L4 4.5 Q5 7 7.5 8 L9 7 L11 9 L9.5 11 Q2 10 1 2.5 Z" fill="var(--blue)"/></svg>
        (888) 555-VXTRL
      </li>
      <li>
        <svg viewBox="0 0 12 12" aria-hidden="true"><rect x="1" y="2.5" width="10" height="7" fill="none" stroke="var(--blue)" stroke-width="1.2"/><path d="M1 2.5 L6 6.5 L11 2.5" fill="none" stroke="var(--blue)" stroke-width="1.2"/></svg>
        dale@vextorial.com
      </li>
      <li>
        <svg viewBox="0 0 12 12" aria-hidden="true"><circle cx="6" cy="6" r="5" fill="none" stroke="var(--blue)" stroke-width="1.1"/><ellipse cx="6" cy="6" rx="2.2" ry="5" fill="none" stroke="var(--blue)" stroke-width="1"/><path d="M1 6 H11" stroke="var(--blue)" stroke-width="1"/></svg>
        <span>www.<span class="site">vextorial</span>.com</span>
      </li>
    </ul>
    <div class="services">Custom Software <span class="services-accent">&middot;</span> Bitcoin Education &amp; Payment Integration</div>
  </section>
</main>
</body>
</html>
```